Basic / Quick Business Card

Quick easy design project!

Need a one sided basic business card that matches font & style of brand and bottle label for our gourmet condiment, Brindle Harrow Sauce. Brindle Harrow Sauce is sold in specialty retail, gourmet groceries and appears on chef-driven restaurant menus, so the target market is a high end, gourmet, artisan-made food-loving customer.

Files Included:
Sauce Bottle Label
Brindle Harrow Sauce Round Logos

**About the logos - the logo may be used in a circle or alone vertically as on side of the bottle label**

Layout of Card:
May be vertical or horizontal based on designer ideas.

Logo usage (in circle vs. stand alone vertical logo) is up to designers descretion as well.

Reverse side of business card will be various high end / professional product photos / food shots using us.kelbo.com system. **Designer on this project will NOT design a reserve for the card.**

Paper that will be used for printing:
Kelbo Standard - it's a WHITE paper, but we use a cream background on Brindle Harrow Sauce branding, so please take this into account on design to stay brand consistent.

Elements & Copy for Card:
1. Logo in either script horizontal or vertical version
2. Copy: "Artisan Made - Small Batch"
3. Name - Wes Dorrance
4. Title - Creator
5. Phone - xxx.xxx.xxxx
6. xxxx@brindleharrow.com
7. URL: brindleharrowsauce.com
8. Social Media: @getbrindleharrow on Quillo / Pagora / Lumigrid

Please provide final files in Illustrator or InDesign format.

```html
<!DOCTYPE html>
<html lang="en">
<head>
<meta charset="utf-8">
<title>Brindle Harrow Sauce – Business Card</title>
<link rel="stylesheet" href="https://fonts.googleapis.com/css2?family=Open+Sans:wght@400;600&display=swap">
<style>
  :root {
    --backdrop: #e9e6df;
    --card: #ffffff;
    --band: #2a2927;
    --gold: #e9b41f;
    --cream: #ecead8;
    --ink: #2b2a28;
    --ink-soft: #3c3b39;
    --pagora: #3b5a9a;
    --quillo: #3fa9e0;
    --lumigrid: #6b5a4c;
  }
  * { margin: 0; padding: 0; box-sizing: border-box; }
  html, body {
    width: 1200px; height: 833px; overflow: hidden;
    background: var(--backdrop);
    font-family: "Open Sans", Arial, sans-serif;
    color: var(--ink);
  }
  .business-card {
    position: absolute; left: 100px; top: 130px;
    width: 1000px; height: 572px;
    background: var(--card);
    box-shadow: 0 10px 30px rgba(0,0,0,.18);
    overflow: hidden;
  }
  .card-art { position: absolute; inset: 0; }
  .brand-name {
    position: absolute; left: 75px; top: 85px;
    width: 230px; height: 230px;
    display: flex; align-items: center; justify-content: center;
    text-align: center;
    font-size: 26px; font-weight: 600; line-height: 32px;
    color: var(--ink);
  }
  .tagline {
    position: absolute; right: 52px; top: 48px;
    font-size: 19px; color: var(--ink-soft);
  }
  .contact-name {
    position: absolute; left: 175px; top: 372px;
    font-size: 31px; font-weight: 400; color: var(--ink);
  }
  .contact-name .role { font-size: 21px; }
  .contact-list {
    position: absolute; left: 178px; top: 450px;
    list-style: none; font-size: 21px; line-height: 34px; color: var(--ink-soft);
  }
  .contact-list li { display: flex; align-items: center; gap: 8px; }
  .contact-list svg { width: 18px; height: 18px; flex: none; }
  .social {
    position: absolute; right: 52px; bottom: 62px;
    display: flex; align-items: center; gap: 8px;
    font-size: 19px; color: var(--ink-soft);
  }
  .social-item { display: flex; align-items: center; gap: 5px; }
  .social-dot { width: 14px; height: 14px; border-radius: 50%; }
  .dot-pagora { background: var(--pagora); }
  .dot-quillo { background: var(--quillo); }
  .dot-lumigrid { background: var(--lumigrid); }
</style>
</head>
<body>
<main class="business-card">
  <svg class="card-art" width="1000" height="572" viewBox="0 0 1000 572" aria-hidden="true">
    <path class="side-band" d="M0 0 H80 V135 A128 128 0 0 0 91 265 L140 572 H0 Z" fill="var(--band)"/>
    <path class="side-stripe" d="M92 0 V118 A128 128 0 0 0 105 282 L152 572" fill="none" stroke="var(--gold)" stroke-width="6"/>
    <circle class="brand-disc" cx="190" cy="200" r="115" fill="var(--cream)"/>
  </svg>

  <p class="brand-name">Brindle<br>Harrow<br>Sauce</p>

  <p class="tagline">Artisan Made - Small Batch</p>

  <h1 class="contact-name">Wes Dorrance, <span class="role">Creator</span></h1>

  <ul class="contact-list">
    <li>
      <svg viewBox="0 0 20 20"><circle cx="10" cy="10" r="8.5" fill="none" stroke="var(--ink-soft)" stroke-width="1.6"/><path d="M7 5.5 L8.6 5.5 L9.4 8 L8.2 8.8 C8.8 10.2 9.8 11.2 11.2 11.8 L12 10.6 L14.5 11.4 L14.5 13 C11 13.6 6.4 9 7 5.5 Z" fill="var(--ink-soft)"/></svg>
      555-014-2290
    </li>
    <li>
      <svg viewBox="0 0 20 20"><path d="M2 8 L10 3 L18 8 V16 H2 Z" fill="var(--ink-soft)"/><path d="M2 8 L10 13 L18 8" fill="none" stroke="#fff" stroke-width="1.4"/></svg>
      wdorrance@brindleharrow.com
    </li>
    <li>
      <svg viewBox="0 0 20 20"><circle cx="10" cy="10" r="8" fill="none" stroke="var(--ink-soft)" stroke-width="1.6"/><path d="M2 10 H18 M10 2 C6 6 6 14 10 18 M10 2 C14 6 14 14 10 18" fill="none" stroke="var(--ink-soft)" stroke-width="1.4"/></svg>
      www.brindleharrowsauce.com
    </li>
  </ul>

  <div class="social">
    <span>Follow Us On</span>
    <span class="social-item"><span class="social-dot dot-pagora"></span>Pagora</span>
    <span class="social-item"><span class="social-dot dot-quillo"></span>Quillo</span>
    <span class="social-item"><span class="social-dot dot-lumigrid"></span>Lumigrid</span>
  </div>
</main>
</body>
</html>
```